NZ First of it's kind solutions directory and marketplace for busy Mums needs a business card design

We need a business card design for our new nationwide business in NZ (long term plans to go global). We provide solutions to the everyday challenges that busy Mums face by connecting them with quality communities and suppliers of carefully selected, relevant products and services. We sell direct via our online marketplace. The final design should communicate our values of inclusivity, quality and smart solutions. Colours should incorporate our logo colour palette of #477077 and #6ba8b2. Our website is at https://www.brightnestmums.example

Target Market(s)

busy Mums, Age 28 – 50, female, income over $100K, location main centres NZ primarily but NZ wide. Is likely juggling work or career with a young family. Probably had hobbies which have fallen by the wayside.
-Wants to succeed in her chosen career without compromising on family life
-to successfully juggle her career without feeling like she is compromising her children
- Is time poor, something always has to give and it’s generally her health (she’ll stay up late, get stressed)
- probably ex corporate or professional career. Has discretional income

Industry/Entity Type

Business

Contact Information for Business Card

Lena Forbisher, Founder, BrightNestMums.example (Strapline Tap; Gather; Sorted), 47 Kowhai Terrace, Ellerslie, Auckland 1051, New Zealand. Mob: 021 483 517 Ph: +64 (0)9 571 4860

Font styles to use
Other font styles liked:
• Raleway, and/or Architects Daughter

Colors
00a990
33b8a4
86cfc6
cfeae6

Requirements
Must have
• the above details, streamline. the logo and colours associated with those logos
Should not have
• foil or metallic colours

```html
<!DOCTYPE html>
<html lang="en">
<head>
<meta charset="utf-8">
<title>BrightNestMums business card</title>
<link rel="stylesheet" href="https://fonts.googleapis.com/css2?family=Work+Sans:wght@400;500;700&display=swap">
<style>
  :root {
    --backdrop: #3a3431;
    --card: #1c1d1f;
    --card-edge: #477077;
    --teal: #6ba8b2;
    --teal-deep: #477077;
    --front-mark: #34363a;
    --ink-light: #f2f2f2;
    --ink-soft: #c9cccd;
  }
  * { box-sizing: border-box; margin: 0; padding: 0; }
  html, body { width: 1200px; height: 715px; overflow: hidden; }
  body {
    background: var(--backdrop);
    font-family: "Work Sans", Arial, sans-serif;
    position: relative;
  }
  .card {
    position: absolute;
    width: 500px;
    height: 286px;
    background: var(--card);
    border-radius: 6px;
    box-shadow: 0 18px 36px rgba(0,0,0,.45);
  }
  .card--front {
    left: 60px; top: 214px;
    border-bottom: 6px solid var(--card-edge);
    border-right: 4px solid var(--card-edge);
    display: flex; align-items: center; justify-content: center; gap: 14px;
  }
  .card--back {
    left: 640px; top: 214px;
    display: flex; align-items: center;
    padding: 0 34px 0 40px;
  }
  .brand {
    display: flex; align-items: center; gap: 10px;
    font-weight: 700; letter-spacing: -0.5px;
  }
  .brand__dot { width: 22px; height: 22px; border-radius: 50%; }
  .card--front .brand { font-size: 38px; color: var(--front-mark); }
  .card--front .brand__dot { background: var(--front-mark); width: 30px; height: 30px; }
  .card--back .brand { font-size: 23px; color: var(--teal); width: 220px; }
  .card--back .brand__dot { background: var(--teal); }
  .divider {
    width: 2px; height: 104px; background: var(--ink-light);
    margin: 0 18px 0 8px;
  }
  .contact { color: var(--ink-light); font-size: 12.5px; line-height: 1.5; letter-spacing: .4px; }
  .contact__name { color: var(--teal); font-size: 21px; font-weight: 500; line-height: 1.1; }
  .contact__role { color: var(--ink-soft); margin-bottom: 4px; }
  .contact__line { display: flex; align-items: center; gap: 6px; }
  .contact__line svg { width: 9px; height: 9px; flex: none; }
</style>
</head>
<body>
  <section class="card card--front" aria-label="Card front">
    <div class="brand"><span class="brand__dot"></span>BrightNestMums</div>
  </section>

  <section class="card card--back" aria-label="Card back">
    <div class="brand"><span class="brand__dot"></span>BrightNestMums</div>
    <div class="divider"></div>
    <div class="contact">
      <p class="contact__name">Lena Forbisher</p>
      <p class="contact__role">Founder</p>
      <p>47 Kowhai Terrace, Ellerslie</p>
      <p>Auckland 1051, New Zealand</p>
      <p class="contact__line">
        <svg viewBox="0 0 10 10"><rect x="2.5" y="0.5" width="5" height="9" rx="1" fill="none" stroke="#c9cccd"/></svg>
        021 483 517</p>
      <p class="contact__line">
        <svg viewBox="0 0 10 10"><path d="M2 1 L4 1 L4.5 3 L3.3 4 Q4.5 6 6 6.7 L7 5.5 L9 6 L9 8 Q5 9 2.5 6.5 Q1 4 2 1Z" fill="#c9cccd"/></svg>
        +64 (0)9 571 4860</p>
      <p class="contact__line">
        <svg viewBox="0 0 10 10"><circle cx="5" cy="5" r="4.2" fill="none" stroke="#c9cccd"/><path d="M1 5 H9 M5 1 V9" stroke="#c9cccd" stroke-width=".8"/></svg>
        www.brightnestmums.example</p>
    </div>
  </section>
</body>
</html>
```